Technical Communications firm needs an article turned into a white paper

We want to redesign a 3-part blog series into a white paper that we can print for a conference. I've consolidated the three posts into the attached Word document.

We are looking for a light, easy to read design. Good use of graphics to support the message. I've added the graphics we used in the original post.

You can view them at
http://www.brightquillpages.com/blog/are-you-satisfied-with-your-dita-solution/

Target Market(s)

Product managers from High-tech, Finance, and Medical industries.

Industry/Entity Type

Information Technology

Colors

Designer to choose colors to be used in the design.

Requirements
Must have
• Must be modern, light, easy to read and slick design. Try to incorporate the graphics provided, but feel free to add more. Must retain the lists and tables.
• Must align with our website/brand.
• Must be easy to read. So not too busy.
• Please move all footnotes to endnotes. You'll need to rework the numbering.
Nice to have
• Awesome coverpage.
Should not have
• Hokey clipart. Not too heavy or hard to read.

```html
<!DOCTYPE html>
<html lang="en">
<head>
<meta charset="utf-8">
<title>Are You Satisfied With Your DITA Solution? — White Paper Cover</title>
<link href="https://fonts.googleapis.com/css2?family=Titillium+Web:wght@400;600;700&display=swap" rel="stylesheet">
<style>
  :root {
    --backdrop: #e9e6e1;
    --paper: #f4f4f5;
    --navy: #123c86;
    --cyan: #1aa3d9;
    --charcoal: #262626;
    --ink: #3a3a3a;
    --photo-sky: #a49c80;
    --photo-hill: #7b7652;
  }
  * { box-sizing: border-box; margin: 0; padding: 0; }
  html, body { width: 1200px; height: 804px; overflow: hidden; }
  body {
    background: var(--backdrop);
    font-family: "Titillium Web", sans-serif;
    display: flex; align-items: center; justify-content: center;
  }
  .cover {
    position: relative;
    width: 524px; height: 740px;
    background: var(--paper);
    box-shadow: 0 10px 30px rgba(0,0,0,.18);
    overflow: hidden;
  }
  .cover-art { position: absolute; inset: 0; }
  .brand {
    position: absolute; top: 46px; right: 40px;
    display: flex; align-items: center; gap: 8px;
    color: var(--navy); font-weight: 700; font-size: 17px;
    letter-spacing: .5px; text-transform: uppercase; line-height: 1;
  }
  .brand-dot {
    width: 26px; height: 26px; border-radius: 50%;
    background: var(--navy);
  }
  .title {
    position: absolute; top: 478px; left: 0; right: 0;
    text-align: center; text-transform: uppercase; line-height: 1.05;
  }
  .title-lead { display: block; color: var(--cyan); font-weight: 400; font-size: 30px; }
  .title-main { display: block; color: var(--navy); font-weight: 700; font-size: 30px; }
  .byline {
    position: absolute; top: 566px; left: 0; right: 0;
    text-align: center; color: var(--ink); line-height: 1.3;
  }
  .byline-author { display: block; font-size: 13px; font-weight: 600; }
  .byline-role { display: block; font-size: 10.5px; }
  .web {
    position: absolute; top: 660px; left: 0; right: 0;
    text-align: center; color: #fff; font-size: 18px; letter-spacing: .6px;
  }
</style>
</head>
<body>
  <article class="cover">
    <svg class="cover-art" width="524" height="740" viewBox="0 0 524 740" aria-hidden="false">
      <defs>
        <linearGradient id="sceneTone" x1="0" y1="0" x2="0" y2="1">
          <stop offset="0" stop-color="var(--photo-sky)"/>
          <stop offset="0.55" stop-color="#8f8b6e"/>
          <stop offset="1" stop-color="var(--photo-hill)"/>
        </linearGradient>
      </defs>
      <!-- top stripes -->
      <polygon class="stripe-navy" points="0,140 300,104 306,116 0,154" fill="var(--navy)"/>
      <polygon class="stripe-cyan" points="318,104 524,80 524,94 324,116" fill="var(--cyan)"/>
      <!-- photo area -->
      <polygon class="cover-photo" role="img"
        aria-label="Photo: a businessman sitting on a chair on a grassy hillside, clutching his head as a colourful cloud of paint bursts above him"
        points="0,158 524,96 524,398 0,460" fill="url(#sceneTone)"/>
      <!-- bottom stripes -->
      <polygon class="stripe-navy" points="214,444 524,408 524,424 222,460" fill="var(--navy)"/>
      <polygon class="stripe-cyan" points="0,470 200,446 206,458 0,482" fill="var(--cyan)"/>
      <!-- footer band -->
      <rect class="footer-band" x="0" y="610" width="524" height="130" fill="var(--charcoal)"/>
      <rect x="0" y="626" width="524" height="4" fill="var(--cyan)"/>
      <rect x="0" y="704" width="524" height="5" fill="var(--cyan)"/>
    </svg>

    <div class="brand"><span class="brand-dot"></span>Brightquill Pages</div>

    <h1 class="title">
      <span class="title-lead">Are you satisfied with</span>
      <span class="title-main">your DITA solution?</span>
    </h1>

    <p class="byline">
      <span class="byline-author">By Dana Whitfield</span>
      <span class="byline-role">President of Brightquill Pages Authoring Solutions Inc.</span>
    </p>

    <p class="web">www.brightquillpages.com</p>
  </article>
</body>
</html>
```